New Business Card Design Project

Use the flyer uploaded and website www.brightoakbuilders.com for inspiration.
List Our Services on Backside of business cards
Marcus Delling
Harborline Builders Inc.
Licensed General Contractors
858-471-6093

Contact Information for Business Card

Use the flyer uploaded and website www.brightoakbuilders.com for inspiration. List Our Services on Backside of business cards Marcus Delling Harborline Builders Inc. Licensed General Contractors 858-471-6093

```html
<!DOCTYPE html>
<html lang="en">
<head>
<meta charset="utf-8">
<title>Harborline Builders – Business Cards</title>
<link href="https://fonts.googleapis.com/css2?family=Roboto:wght@400;500;700&family=Roboto+Condensed:wght@700&display=swap" rel="stylesheet">
<style>
  :root{
    --stage:#232323;
    --card-dark:#1f1f25;
    --card-light:#ffffff;
    --red:#e81b24;
    --blue:#5b85d0;
    --ink:#1a1a1a;
    --white:#ffffff;
  }
  *{margin:0;padding:0;box-sizing:border-box}
  html,body{width:1200px;height:780px;overflow:hidden;background:var(--stage)}
  body{font-family:"Roboto",Arial,sans-serif;position:relative}
  .card{position:absolute;top:236px;width:540px;height:309px;overflow:hidden;box-shadow:0 14px 30px rgba(0,0,0,.55)}
  .card-front{left:40px;background:var(--card-dark)}
  .card-back{left:620px;background:var(--card-light)}

  .front-swoosh{position:absolute;inset:0}
  .brand-name{position:absolute;font-family:"Roboto",Arial,sans-serif;font-weight:400;text-transform:uppercase;white-space:nowrap}
  .card-front .brand-name{left:290px;width:230px;top:48px;text-align:center;font-size:16px;letter-spacing:2px;color:var(--white)}
  .holder-name{position:absolute;left:72px;top:92px;font-family:"Roboto Condensed",Arial,sans-serif;font-weight:700;font-size:34px;color:var(--red);line-height:1;white-space:nowrap}
  .holder-title{position:absolute;left:74px;top:132px;font-size:13px;color:var(--white);letter-spacing:.2px;white-space:nowrap}
  .divider{position:absolute;left:290px;top:150px;width:1px;height:84px;background:var(--red)}
  .contact-list{position:absolute;left:306px;top:150px;list-style:none}
  .contact-list li{display:flex;align-items:center;gap:8px;font-size:14px;color:var(--white);height:27px;white-space:nowrap}
  .contact-list svg{width:14px;height:14px;flex:none}
  .company-line{position:absolute;left:170px;top:272px;font-size:15px;color:var(--white);white-space:nowrap}

  .card-back .brand-name{left:0;right:0;top:40px;text-align:center;font-size:26px;letter-spacing:3px;color:var(--ink)}
  .guarantee{position:absolute;left:0;right:0;top:96px;text-align:center;font-family:"Roboto Condensed",Arial,sans-serif;font-weight:700;font-size:19px;color:var(--red)}
  .specialty-rule{position:absolute;left:40px;right:40px;top:134px;display:flex;align-items:center;gap:10px}
  .specialty-rule::before,.specialty-rule::after{content:"";flex:1;height:2px;background:var(--blue)}
  .specialty-rule span{font-family:"Roboto Condensed",Arial,sans-serif;font-weight:700;font-size:16px;color:var(--blue)}
  .service-list{position:absolute;left:30px;right:30px;top:166px;list-style:none;display:flex;flex-wrap:wrap;justify-content:center;column-gap:12px;row-gap:9px}
  .service-list li{display:flex;align-items:center;gap:4px;font-size:12.5px;font-weight:500;color:var(--ink);white-space:nowrap}
  .service-list svg{width:11px;height:11px;flex:none}
</style>
</head>
<body>

<section class="card card-front" aria-label="Business card front">
  <svg class="front-swoosh" viewBox="0 0 540 309" preserveAspectRatio="none" aria-hidden="true">
    <path d="M0 32 C 50 200 240 290 540 296 L540 309 L0 309 Z" fill="var(--red)"/>
    <path d="M24 40 C 80 190 250 268 510 282" fill="none" stroke="var(--blue)" stroke-width="4" stroke-linecap="round"/>
  </svg>
  <div class="brand-name">Harborline Builders</div>
  <h1 class="holder-name">Marcus Delling</h1>
  <p class="holder-title">Licensed General Contractors</p>
  <div class="divider"></div>
  <ul class="contact-list">
    <li><svg viewBox="0 0 16 16"><path d="M4 1.5l2.3 3-1.4 1.6c.8 1.9 2.2 3.3 4 4.1l1.6-1.4 3 2.3-1.3 2.4C7.3 13.4 2.5 8.7 1.6 3z" fill="var(--red)"/></svg>858-471-6093</li>
    <li><svg viewBox="0 0 16 16"><rect x="1.5" y="3.5" width="13" height="9" rx="1" fill="var(--red)"/><path d="M2 4l6 5 6-5" fill="none" stroke="var(--card-dark)" stroke-width="1.2"/></svg>info@brightoakbuilders.com</li>
    <li><svg viewBox="0 0 16 16"><circle cx="8" cy="8" r="6.5" fill="var(--red)"/><path d="M1.5 8h13M8 1.5c-2.5 3-2.5 10 0 13M8 1.5c2.5 3 2.5 10 0 13" fill="none" stroke="var(--card-dark)" stroke-width="1"/></svg>www.brightoakbuilders.com</li>
  </ul>
  <p class="company-line">Harborline Builders Inc.</p>
</section>

<section class="card card-back" aria-label="Business card back">
  <div class="brand-name">Harborline Builders</div>
  <p class="guarantee">OUR SERVICES ARE 100% GUARANTEED</p>
  <div class="specialty-rule"><span>SPECIALIZING IN:</span></div>
  <ul class="service-list">
    <li><svg viewBox="0 0 12 12"><circle cx="6" cy="6" r="5" fill="none" stroke="var(--red)"/><path d="M3.5 6l1.8 1.8L8.7 4" fill="none" stroke="var(--red)" stroke-width="1.3"/></svg>Remodel: Kitchen &amp; Bath</li>
    <li><svg viewBox="0 0 12 12"><circle cx="6" cy="6" r="5" fill="none" stroke="var(--red)"/><path d="M3.5 6l1.8 1.8L8.7 4" fill="none" stroke="var(--red)" stroke-width="1.3"/></svg>Painting: Interior &amp; Exterior</li>
    <li><svg viewBox="0 0 12 12"><circle cx="6" cy="6" r="5" fill="none" stroke="var(--red)"/><path d="M3.5 6l1.8 1.8L8.7 4" fill="none" stroke="var(--red)" stroke-width="1.3"/></svg>Flooring: Carpet, Vinyl, Wood</li>
    <li><svg viewBox="0 0 12 12"><circle cx="6" cy="6" r="5" fill="none" stroke="var(--red)"/><path d="M3.5 6l1.8 1.8L8.7 4" fill="none" stroke="var(--red)" stroke-width="1.3"/></svg>Window &amp; Door Replacement</li>
    <li><svg viewBox="0 0 12 12"><circle cx="6" cy="6" r="5" fill="none" stroke="var(--red)"/><path d="M3.5 6l1.8 1.8L8.7 4" fill="none" stroke="var(--red)" stroke-width="1.3"/></svg>Plumbing: Repairs &amp; Upgrades</li>
    <li><svg viewBox="0 0 12 12"><circle cx="6" cy="6" r="5" fill="none" stroke="var(--red)"/><path d="M3.5 6l1.8 1.8L8.7 4" fill="none" stroke="var(--red)" stroke-width="1.3"/></svg>Energy-Efficient Upgrades</li>
    <li><svg viewBox="0 0 12 12"><circle cx="6" cy="6" r="5" fill="none" stroke="var(--red)"/><path d="M3.5 6l1.8 1.8L8.7 4" fill="none" stroke="var(--red)" stroke-width="1.3"/></svg>Deck &amp; Patio Construction</li>
    <li><svg viewBox="0 0 12 12"><circle cx="6" cy="6" r="5" fill="none" stroke="var(--red)"/><path d="M3.5 6l1.8 1.8L8.7 4" fill="none" stroke="var(--red)" stroke-width="1.3"/></svg>Water &amp; Mold Damage</li>
    <li><svg viewBox="0 0 12 12"><circle cx="6" cy="6" r="5" fill="none" stroke="var(--red)"/><path d="M3.5 6l1.8 1.8L8.7 4" fill="none" stroke="var(--red)" stroke-width="1.3"/></svg>Garage Renovation</li>
  </ul>
</section>

</body>
</html>
```